Tandem Hearth Works Pty Ltd

We need business cards for a company based in Perth, we install, service and maintain fire equipment.
On the front we want a great design with our logo and a small spot for our full company name, general company email address and office number. On the back we need space for our name, title, mobile number and email address on the back.

Target Market(s)

Facility managers and commercial/industrial building owners/occupiers.

Contact Information for Business Card

Font styles to use
Sans Serif

Requirements
Must have
• Please only submit 5 of your best samples.
Darker tones are preferred.
Nice to have
• We want to use, black, red and grey. Keep it modern and clean.
I've attached the company logo and a sample of a boarder we use on our emergency plans.
Should not have
• No preference. Let the designer choose.

```html
<!DOCTYPE html>
<html lang="en">
<head>
<meta charset="utf-8">
<title>Tandem Hearth Works – Business Cards</title>
<link rel="stylesheet" href="https://fonts.googleapis.com/css2?family=Arimo:wght@400;700&display=swap">
<style>
  :root {
    --backdrop: #1b1b1b;
    --card-red: #ed1c24;
    --ink-white: #ffffff;
    --rule-white: rgba(255, 255, 255, 0.85);
  }
  * { box-sizing: border-box; margin: 0; padding: 0; }
  html, body {
    width: 1093px;
    height: 1200px;
    overflow: hidden;
    background: var(--backdrop);
    font-family: "Arimo", Arial, sans-serif;
    color: var(--ink-white);
  }
  .sheet { position: relative; width: 1093px; height: 1200px; }
  .card {
    position: absolute;
    left: 264px;
    width: 580px;
    height: 357px;
    background: var(--card-red);
    text-align: center;
  }
  .card--front { top: 226px; }
  .card--back { top: 620px; }

  .wordmark {
    position: absolute;
    top: 82px;
    left: 0;
    right: 0;
    font-weight: 700;
    font-size: 96px;
    line-height: 1;
    letter-spacing: 2px;
  }
  .person-name {
    position: absolute;
    top: 214px;
    left: 0; right: 0;
    font-weight: 700;
    font-size: 25px;
    line-height: 1;
  }
  .person-title {
    position: absolute;
    top: 240px;
    left: 0; right: 0;
    font-size: 19px;
    line-height: 1;
  }
  .divider {
    position: absolute;
    top: 277px;
    left: 209px;
    width: 160px;
    height: 1px;
    background: var(--rule-white);
  }
  .contact-row {
    position: absolute;
    left: 0; right: 0;
    display: flex;
    justify-content: center;
    align-items: center;
    gap: 14px;
    font-size: 19px;
    line-height: 1;
  }
  .contact-row--front { top: 290px; }
  .contact-row--back { top: 239px; font-size: 18px; gap: 18px; }
  .contact-item { display: flex; align-items: center; gap: 6px; }
  .icon { fill: var(--ink-white); display: block; }

  .company-name {
    position: absolute;
    top: 108px;
    left: 0; right: 0;
    font-weight: 700;
    font-size: 25px;
    line-height: 29px;
  }
  .office-phone {
    position: absolute;
    top: 184px;
    left: 0; right: 0;
    font-weight: 700;
    font-size: 28px;
    line-height: 1;
  }
</style>
</head>
<body>
<main class="sheet">
  <section class="card card--front">
    <div class="wordmark">THW</div>
    <h1 class="person-name">MARCUS ELLERY</h1>
    <p class="person-title">Managing Director</p>
    <div class="divider"></div>
    <div class="contact-row contact-row--front">
      <span class="contact-item">
        <svg class="icon" width="14" height="20" viewBox="0 0 14 20" aria-hidden="true">
          <path d="M2 0h10a2 2 0 0 1 2 2v16a2 2 0 0 1-2 2H2a2 2 0 0 1-2-2V2a2 2 0 0 1 2-2zm0 3v12h10V3zm5 13.2a1 1 0 1 0 0 2a1 1 0 0 0 0-2z"/>
        </svg>
        555.0142.0178
      </span>
      <span class="contact-item">
        <svg class="icon" width="20" height="14" viewBox="0 0 20 14" aria-hidden="true">
          <path d="M0 0h20v1.5L10 8 0 1.5zM0 3.2l6.5 4.3L0 13zm20 0v9.8l-6.5-5.5zM7.8 8.4 10 9.9l2.2-1.5L19.3 14H.7z"/>
        </svg>
        name@thw.com
      </span>
    </div>
  </section>

  <section class="card card--back">
    <h2 class="company-name">TANDEM HEARTH<br>WORKS PTY LTD</h2>
    <p class="office-phone">555.0190.0190</p>
    <div class="contact-row contact-row--back">
      <span class="contact-item">
        <svg class="icon" width="18" height="13" viewBox="0 0 20 14" aria-hidden="true">
          <path d="M0 0h20v1.5L10 8 0 1.5zM0 3.2l6.5 4.3L0 13zm20 0v9.8l-6.5-5.5zM7.8 8.4 10 9.9l2.2-1.5L19.3 14H.7z"/>
        </svg>
        info@thw.com
      </span>
      <span class="contact-item">
        <svg class="icon" width="17" height="17" viewBox="0 0 20 20" aria-hidden="true">
          <path d="M10 0a10 10 0 1 0 0 20a10 10 0 0 0 0-20zm-1 2.2V6H6.3C7 4 8 2.7 9 2.2zm2 0c1 .5 2 1.8 2.7 3.8H11zM6.9 2.7A11 11 0 0 0 4.2 6H3.1a8 8 0 0 1 3.8-3.3zm6.2 0A8 8 0 0 1 16.9 6h-1.1a11 11 0 0 0-2.7-3.3zM2.3 8h1.6a15 15 0 0 0 0 4H2.3a8 8 0 0 1 0-4zm3.6 0H9v4H5.9a13 13 0 0 1 0-4zM11 8h3.1a13 13 0 0 1 0 4H11zm5.1 0h1.6a8 8 0 0 1 0 4h-1.6a15 15 0 0 0 0-4zM3.1 14h1.1a11 11 0 0 0 2.7 3.3A8 8 0 0 1 3.1 14zm3.2 0H9v3.8C8 17.3 7 16 6.3 14zM11 14h2.7c-.7 2-1.7 3.3-2.7 3.8zm4.8 0h1.1a8 8 0 0 1-3.8 3.3a11 11 0 0 0 2.7-3.3z"/>
        </svg>
        www.thw.com
      </span>
    </div>
  </section>
</main>
</body>
</html>
```